Large online photo magazine needs redesign

We have previously digitised a historical photographic magazine of around 20,000 printed pages and made it available online. The magazine ran up to the early 1970s, and the content is largely black and white photographs of local events, accompanied by short captions.

Although the content is very rich, the design needs to be revisited so that:
* it is visually appealing
* it is responsive (i.e. works in browsers across all manner of devices)
* is faithful to the nature of the content

There are only a few core page types, and the central one is the article page, an example of which can be seen at:
http://snapgazette.example/gisborne/issue/KLR48_19600714/t1-body-d4.html

Any design submitted should be based on the treatment of an article page such as the above.

Given the large number of pages on our site, we need a design which can be templated to work for any content in the collection, i.e. we cannot hand-craft our templates to match a given page of content, rather a template must work acceptably well for all content.

The current site, although basic in design, has the advantage that it is quite efficient in the amount of data per page request (around 100k - 200k). While not adverse to web fonts, banner imagery etc, we will carefully consider the benefit gained from any such treatment against the amount of extra data that needs to be downloaded to the client's browser.

For the right design, we are able ourselves to adapt it to a CSS layout.

An example of each core page type is as follows (though for this project we only expect a design for a single page, as itemised above):

http://snapgazette.example/gisborne/index.html
http://snapgazette.example/gisborne/about.html
http://snapgazette.example/gisborne/help.html
http://snapgazette.example/gisborne/initial/index.html
http://snapgazette.example/gisborne/search/results?type=section&text=smith&cmdSubmit=Go
http://snapgazette.example/gisborne/advanced-search/index.html
http://snapgazette.example/gisborne/issue/KLR48_19600714/t1-front-d1.html
http://snapgazette.example/gisborne/issue/KLR48_19600714/index.html
http://snapgazette.example/gisborne/issue/KLR48_19600714/fig-KLR48_19600714_005a.html
http://snapgazette.example/gisborne/issue/KLR48_19600714/KLR48_19600714_012.html
http://snapgazette.example/gisborne/issue/KLR48_19600714/thumbnails.html

Target Market(s)

A general browsing audience of all ages, but skewed towards the older generations, and those interested in family / regional history.

The average user will not be particularly web-savy, and the treatment of the content should not detract / distract from the actual content itself.

Industry/Entity Type

Events

Requirements
Must have
• * it is visually appealing
The content should be visually appealing to the audience, which can be defined as a general browsing audience of all ages, but skewed towards the middle and older generations.

* it is responsive (the design can be adapted - by us - to work in browsers across all manner of devices)

The magazine covers (http://snapgazette.example/gisborne/issues/index.html) offer some possible inspiration for treatment of the material.

```html
<!DOCTYPE html>
<html lang="en">
<head>
<meta charset="utf-8">
<title>Snap Gazette — Issue 73, July 14, 1960</title>
<link rel="stylesheet" href="https://fonts.googleapis.com/css2?family=Source+Sans+3:wght@400;600;700&display=swap">
<style>
:root{
  --brand:#c83e55;
  --brand-dark:#8e2436;
  --ink:#222;
  --footer:#4a4a4a;
  --paper:#fff;
  --search-btn:#4d4d4d;
  --photo-light:#c9c4b0;
  --photo-dark:#5c5a50;
}
*{box-sizing:border-box;margin:0;padding:0}
html,body{width:1165px;height:1200px;overflow:hidden;background:var(--paper);font-family:"Source Sans 3",Arial,sans-serif;color:var(--ink)}
a{text-decoration:none;color:inherit}
.site-header{position:absolute;left:0;top:0;width:1165px;height:200px;background:var(--brand)}
.nav-band{position:absolute;left:0;top:148px;width:100%;height:52px;background:linear-gradient(to bottom,var(--brand),var(--brand-dark))}
.brand{position:absolute;left:107px;top:68px;display:flex;align-items:center;gap:14px;color:#fff;font-weight:700;font-size:44px;letter-spacing:1px}
.brand-mark{width:26px;height:26px;background:#fff}
.search{position:absolute;left:729px;top:70px;display:flex;gap:6px}
.search input{width:218px;height:32px;border:1px solid #ddd;background:#fff}
.search button{width:32px;height:32px;border:0;background:var(--search-btn);display:flex;align-items:center;justify-content:center}
.main-nav{position:absolute;left:118px;top:163px;display:flex;gap:23px;font-size:14px;color:#fff}
.main-nav a:nth-child(3){margin-left:10px}
.issue-tools{position:absolute;left:93px;top:213px;display:flex;gap:9px}
.tool{width:131px;height:35px;background:var(--brand);border-radius:3px;color:#fff;font-size:18px;display:flex;align-items:center;justify-content:center;gap:10px}
.articles{position:absolute;left:95px;top:286px;display:grid;grid-template-columns:311px 311px 311px;column-gap:14px;row-gap:0;grid-auto-rows:423px}
.card{border-top:5px solid var(--brand)}
.card-photo{display:block;height:151px;margin-top:2px;background:linear-gradient(135deg,var(--photo-light),#9d9886 55%,var(--photo-dark))}
.card-title{margin-top:17px;font-size:18px;font-weight:700;color:var(--brand);line-height:24px;text-align:justify;text-align-last:left}
.card-date{margin-top:7px;font-size:11px;color:var(--brand)}
.card-text{margin-top:10px;font-size:11px;line-height:24px;height:72px;overflow:hidden;text-align:justify}
.read-more{display:block;margin-top:17px;font-size:13px;color:var(--brand)}
.pager{position:absolute;left:1010px;top:1067px;display:flex;gap:3px}
.pager span{width:20px;height:20px;background:#555;display:flex;align-items:center;justify-content:center}
.site-footer{position:absolute;left:0;top:1093px;width:1165px;height:107px;background:var(--footer);color:#fff}
.footer-nav{position:absolute;left:97px;top:21px;display:flex;gap:35px;font-size:14px}
.footer-nav a:last-child{margin-left:12px}
.copyright{position:absolute;left:95px;top:43px;font-size:11px}
.social{position:absolute;left:905px;top:34px;display:flex;gap:1px}
.social span{width:36px;height:36px;border-radius:50%;background:#fff}
</style>
</head>
<body>
<header class="site-header">
  <div class="nav-band"></div>
  <a class="brand" href="#"><span class="brand-mark"></span>Snap Gazette</a>
  <form class="search">
    <input type="text" aria-label="Search">
    <button type="button" aria-label="Search">
      <svg width="13" height="13" viewBox="0 0 13 13"><circle cx="5.5" cy="5.5" r="4" fill="none" stroke="#fff" stroke-width="2"/><line x1="8.5" y1="8.5" x2="12" y2="12" stroke="#fff" stroke-width="2"/></svg>
    </button>
  </form>
  <nav class="main-nav">
    <a href="#">HOME</a><a href="#">ABOUT</a><a href="#">BROWSE SNAP GAZETTE</a><a href="#">A-Z PEOPLE</a>
  </nav>
</header>

<div class="issue-tools">
  <a class="tool" href="#"><svg width="22" height="14" viewBox="0 0 22 14"><path d="M10 1 4 7l6 6M18 1l-6 6 6 6" fill="none" stroke="#fff" stroke-width="3"/></svg>Prev</a>
  <a class="tool" href="#">Next<svg width="22" height="14" viewBox="0 0 22 14"><path d="M4 1l6 6-6 6M12 1l6 6-6 6" fill="none" stroke="#fff" stroke-width="3"/></svg></a>
  <a class="tool" href="#">Issue content</a>
  <a class="tool" href="#"><svg width="28" height="26" viewBox="0 0 28 26"><rect x="7" y="1" width="14" height="7" fill="#fff"/><rect x="1" y="8" width="26" height="11" rx="2" fill="#fff"/><rect x="7" y="15" width="14" height="10" fill="#fff" stroke="#c83e55" stroke-width="2"/></svg>Print</a>
</div>

<main class="articles">
  <article class="card">
    <span class="card-photo" role="img" aria-label="Black and white portrait of an air hostess in uniform cap"></span>
    <h2 class="card-title">This is probably something of a record--three sisters</h2>
    <p class="card-date">No 73 July 14, 1960</p>
    <p class="card-text">This is probably something of a record--three sisters who are all air hostesses. They are the Harlow sisters.....Maribel, Edith, and Rosalind, daughters of Mr and Mrs R. T. Harlow, of the town.</p>
    <a class="read-more" href="#">READ MORE</a>
  </article>
  <article class="card">
    <span class="card-photo" role="img" aria-label="Black and white photograph of a truss bridge over a river"></span>
    <h2 class="card-title">This is probably something of a record--three sisters</h2>
    <p class="card-date">No 73 July 14, 1960</p>
    <p class="card-text">This is probably something of a record--three sisters who are all air hostesses. They are the Harlow sisters.....Maribel, Edith, and Rosalind, daughters of Mr and Mrs R. T. Harlow, of the town.</p>
    <a class="read-more" href="#">READ MORE</a>
  </article>
  <article class="card">
    <span class="card-photo" role="img" aria-label="Engagement portrait of a young couple beside a printed notice"></span>
    <h2 class="card-title">This is probably something of a record--three sisters</h2>
    <p class="card-date">No 73 July 14, 1960</p>
    <p class="card-text">This is probably something of a record--three sisters who are all air hostesses. They are the Harlow sisters.....Maribel, Edith, and Rosalind, daughters of Mr and Mrs R. T. Harlow, of the town.</p>
    <a class="read-more" href="#">READ MORE</a>
  </article>
  <article class="card">
    <span class="card-photo" role="img" aria-label="Magazine page with two portraits and engagement notices"></span>
    <h2 class="card-title">This is probably something of a record--three sisters</h2>
    <p class="card-date">No 73 July 14, 1960</p>
    <p class="card-text">This is probably something of a record--three sisters who are all air hostesses. They are the Harlow sisters.....Maribel, Edith, and Rosalind, daughters of Mr and Mrs R. T. Harlow, of the town.</p>
    <a class="read-more" href="#">READ MORE</a>
  </article>
  <article class="card">
    <span class="card-photo" role="img" aria-label="Two engagement portraits of young couples"></span>
    <h2 class="card-title">This is probably something of a record--three sisters</h2>
    <p class="card-date">No 73 July 14, 1960</p>
    <p class="card-text">This is probably something of a record--three sisters who are all air hostesses. They are the Harlow sisters.....Maribel, Edith, and Rosalind, daughters of Mr and Mrs R. T. Harlow, of the town.</p>
    <a class="read-more" href="#">READ MORE</a>
  </article>
  <article class="card">
    <span class="card-photo" role="img" aria-label="Crowd watching children's traffic training in a town street"></span>
    <h2 class="card-title">This is probably something of a record--three sisters</h2>
    <p class="card-date">No 73 July 14, 1960</p>
    <p class="card-text">This is probably something of a record--three sisters who are all air hostesses. They are the Harlow sisters.....Maribel, Edith, and Rosalind, daughters of Mr and Mrs R. T. Harlow, of the town.</p>
    <a class="read-more" href="#">READ MORE</a>
  </article>
</main>

<nav class="pager" aria-label="Pages">
  <span><svg width="8" height="10" viewBox="0 0 8 10"><path d="M6 1 2 5l4 4" fill="none" stroke="#fff" stroke-width="1.5"/></svg></span>
  <span><svg width="8" height="10" viewBox="0 0 8 10"><path d="M2 1l4 4-4 4" fill="none" stroke="#fff" stroke-width="1.5"/></svg></span>
</nav>

<footer class="site-footer">
  <nav class="footer-nav"><a href="#">Home</a><a href="#">About</a><a href="#">Browse Snap Gazette</a><a href="#">A-Z people</a></nav>
  <p class="copyright">© 2014 Company Name.&nbsp; All right reserved.&nbsp; Term of Use</p>
  <div class="social"><span></span><span></span><span></span><span></span></div>
</footer>
</body>
</html>
```